RV7 - Rapid Vigil Field Operations Suite

I need an introductory website for RV7 which describes the features of the product and the ease of use of the product. The product is focused on Preparing for an incident using Volunteer and Resource management and then responding to an incident with Incident Management, Team Management, Task Management and Communication Management. Once a situation is handled, the application provides complete reporting on each of the above aspects

Target Market(s)

Local Government entities, specifically the emergency department directors or coordinators

Industry/Entity Type

Government Office

Coding

Coded - Design and coding required

Font styles to use
Sans Serif

Requirements
Must have
• Clear layout with modern images. I want to be able to get a clear understanding of the features of the product and the ease of use. I would like to high light how the application helps in Communication Management, Team Management, Task Management and Incident Managements. Also, how the use of application helps to get an immediate snap shot of how well an incident was handled. I want to highlight how the Dashboard provides a quick look at the Incident(s) being managed
Nice to have
• I would like to in the future add videos to the site. At this point don't have any ideas about nice to have features
Should not have
• traditional designs. I am looking for a slick, modern looking website. Clean design is the key.

```html
<!DOCTYPE html>
<html lang="en">
<head>
<meta charset="utf-8">
<title>RV7 - Rapid Vigil Field Operations Suite</title>
<link href="https://fonts.googleapis.com/css2?family=Roboto:wght@400;500;700&family=Roboto+Condensed:wght@400;700&display=swap" rel="stylesheet">
<style>
:root{
  --blue:#2b5ea7;
  --blue-dark:#234f8e;
  --app-blue:#1f4fd0;
  --green:#9bc72b;
  --green-dark:#86b020;
  --ink:#333;
  --muted:#666;
  --footer:#2b2b2b;
  --white:#fff;
}
*{box-sizing:border-box;margin:0;padding:0}
html,body{width:674px;height:1200px;overflow:hidden}
body{font-family:'Roboto',sans-serif;color:var(--ink);background:var(--white);position:relative}
.abs{position:absolute}
.cond{font-family:'Roboto Condensed',sans-serif}

/* header */
.site-header{position:absolute;left:0;top:0;width:674px;height:62px;background:var(--white)}
.contact-bar{left:335px;top:0;width:259px;height:14px;background:var(--green);color:var(--white);font-size:6.6px;display:flex;align-items:center;justify-content:space-around;padding:0 8px}
.brand{left:96px;top:8px;display:flex;align-items:center;gap:8px}
.brand-mark{width:34px;height:34px;border:3px solid var(--blue);border-radius:4px}
.brand-name{font-family:'Roboto Condensed',sans-serif;font-weight:700;font-size:30px;color:var(--blue);letter-spacing:2px;line-height:1}
.brand-tag{left:148px;top:47px;font-size:4.8px;color:var(--blue)}
.main-nav{left:289px;top:44px;display:flex;gap:14px;font-size:7px;color:var(--blue)}
.main-nav .active{color:var(--green);border-bottom:1px solid var(--green);padding-bottom:10px}

/* hero */
.hero{left:0;top:62px;width:674px;height:240px;background:linear-gradient(135deg,#4a4540 0%,#2a2623 45%,#3b3733 100%)}
.hero h1{position:absolute;left:0;width:674px;top:104px;text-align:center;color:var(--white);font-family:'Roboto Condensed',sans-serif;font-weight:400;font-size:12.5px;line-height:16px}
.store-btns{position:absolute;left:281px;top:151px;display:flex;gap:5px}
.store-btn{width:51px;height:17px;background:#111;border:1px solid #888;border-radius:3px;color:var(--white);font-size:5.5px;display:flex;align-items:center;justify-content:center}
.dots{position:absolute;left:316px;top:213px;display:flex;gap:4px}
.dots span{width:5px;height:5px;border-radius:50%;background:var(--white)}
.dots span.on{background:var(--blue);border:1px solid var(--white)}

/* intro */
.section-title{position:absolute;left:0;width:674px;text-align:center;font-family:'Roboto Condensed',sans-serif;font-weight:700;font-size:12.5px}
.intro-title{top:317px;color:var(--blue)}
.intro-copy{position:absolute;left:0;top:343px;width:674px;text-align:center;font-size:6.6px;line-height:10.5px;color:var(--ink)}
.role{position:absolute;left:140px}
.role h3{font-size:8px;font-weight:500;color:var(--ink);padding-left:16px;position:relative}
.role h3::before{content:"";position:absolute;left:2px;top:1px;width:7px;height:7px;border:1.4px solid var(--ink);border-radius:50%}
.role p{font-size:6.2px;color:var(--muted);padding-left:16px;margin-top:3px}
.web-panel{left:357px;top:392px;width:70px;height:108px;background:var(--white);box-shadow:0 1px 4px rgba(0,0,0,.25)}
.web-panel .bar{height:26px;background:var(--app-blue);color:var(--white);font-size:5.5px;padding:15px 0 0 6px}
.mobile-panel{left:420px;top:384px;width:109px;height:187px;background:#777;box-shadow:0 2px 8px rgba(0,0,0,.35)}
.mobile-drawer{position:absolute;left:0;top:0;width:85px;height:187px;background:var(--app-blue);color:var(--white)}
.mobile-drawer .user{padding:30px 0 0 5px;font-size:5.5px;font-weight:500}
.mobile-drawer ul{list-style:none;margin-top:10px;font-size:4.6px}
.mobile-drawer li{padding:4px 0 4px 21px}
.mobile-drawer li.sel{background:#2d5ad8;color:#f5d34a}
.badge-circle{position:absolute;border-radius:50%;color:var(--white);font-size:6px;display:flex;align-items:center;justify-content:center;text-align:center;line-height:7px}
.btn{position:absolute;height:17px;color:var(--white);font-size:6.2px;font-weight:500;display:flex;align-items:center;justify-content:center}
.btn-blue{background:var(--blue)}
.btn-green{background:var(--green)}

/* respond */
.respond{left:0;top:644px;width:674px;height:270px;background:var(--green)}
.respond-title{top:666px;color:var(--white)}
.task-screen{left:287px;top:707px;width:99px;height:176px;background:#f2f2f2}
.task-screen .bar{height:25px;background:var(--app-blue);color:var(--white);font-size:5.3px;padding:12px 0 0 14px}
.task-card{margin:4px 4px 0;height:33px;background:var(--white);border-top:2px solid var(--app-blue);font-size:4.6px;padding:3px 4px;position:relative}
.task-card b{display:block;font-size:6.4px;color:#333;margin-top:3px;font-weight:500}
.task-card i{position:absolute;right:3px;bottom:2px;font-style:normal;font-size:3.4px;color:#777}
.fab{position:absolute;left:79px;top:155px;width:14px;height:14px;border-radius:50%;background:#f5c518;font-size:8px;display:flex;align-items:center;justify-content:center}
.feature{position:absolute;width:120px;color:var(--white)}
.feature h3{font-size:8.6px;font-weight:500}
.feature p{font-size:6.2px;line-height:7.5px;margin-top:8px;color:#f2f7e4}
.feature.left{text-align:right}
.icon-ring{position:absolute;width:24px;height:24px;border:2px solid var(--white);border-radius:50%}

/* why / reports */
.why{left:0;top:914px;width:674px;height:204px;background:var(--blue)}
.why h2{position:absolute;font-family:'Roboto Condensed',sans-serif;font-weight:700;font-size:12.5px;color:var(--white)}
.why ul{position:absolute;list-style:none;color:var(--white);font-size:6px}
.why ul li{position:relative;padding-left:11px}
.why ul li::before{content:"";position:absolute;left:1px;top:2px;width:4px;height:4px;border-radius:50%;background:var(--white)}
.divider{left:337px;top:928px;width:1px;height:170px;background:#5b83bf}
.sub li{padding-left:11px!important}
.sub li::before{border-radius:0!important;width:3px!important;height:3px!important}
.arrow{position:absolute;left:354px;color:var(--white);font-size:6px}

/* footer */
.site-footer{left:0;top:1118px;width:674px;height:82px;background:var(--footer)}
.foot-nav{position:absolute;left:0;top:14px;width:674px;display:flex;justify-content:center;gap:14px;color:var(--white);font-size:6.6px}
.social{position:absolute;left:234px;top:34px;display:flex;gap:11px}
.social span{width:15px;height:15px;border-radius:50%;background:var(--white)}
.social span.hl{background:var(--blue);box-shadow:0 0 0 2px var(--white)}
.copy{position:absolute;left:0;top:62px;width:674px;text-align:center;font-size:5.8px;color:#bbb}
</style>
</head>
<body>

<header class="site-header">
  <div class="abs contact-bar"><span>&#9679; Dana Whitfield, PhD</span><span>&#9742; 555-014-2290</span><span>&#9993; dana.whitfield@example.com</span></div>
  <div class="abs brand"><span class="brand-mark"></span><span class="brand-name">RV7</span></div>
  <div class="abs brand-tag">Rapid Vigil Field Operations Suite</div>
  <nav class="abs main-nav">
    <span class="active">Home</span><span>About Us</span><span>Resource management</span><span>Volunteer</span><span>Testimonials</span><span>Contact Us</span>
  </nav>
</header>

<section class="abs hero" role="img" aria-label="Photo of a desk with a smartphone, keyboard, notebook and coffee cup">
  <h1>RV7 – Assisting CERT Community in Emergency<br>Command, Control and Coordination</h1>
  <div class="store-btns"><span class="store-btn">Get it for Phones</span><span class="store-btn">Get it for Tablets</span></div>
  <div class="dots"><span></span><span class="on"></span><span></span><span></span><span></span></div>
</section>

<h2 class="section-title intro-title">RV7 INTRODUCTION</h2>
<p class="intro-copy">RV7 offers a web based and mobile interface to assist the CERT Community.<br>The roles from CERT teams have been created to have access to either the web, mobile or both the interfaces</p>

<svg class="abs" style="left:0;top:380px" width="674" height="200" aria-hidden="true">
  <g fill="none" stroke-width="0.8" stroke-dasharray="2 2">
    <path d="M184 54 H333 V96 H357" stroke="#2b5ea7"/>
    <path d="M238 96 H333" stroke="#2b5ea7"/>
    <path d="M245 101 H376 V125 H398" stroke="#9bc72b"/>
    <path d="M198 141 H376 V125" stroke="#9bc72b"/>
  </g>
  <path d="M350 90 L357 96 L350 102" fill="none" stroke="#2b5ea7" stroke-width="0.8"/>
  <path d="M391 119 L398 125 L391 131" fill="none" stroke="#9bc72b" stroke-width="0.8"/>
</svg>

<div class="role" style="top:428px"><h3>Admin</h3><p>Lorem Ipsum is simply dum my text of the</p></div>
<div class="role" style="top:471px"><h3>Incident Commander</h3><p>Lorem Ipsum is simply dum my text of the</p></div>
<div class="role" style="top:513px"><h3>Volunteers</h3><p>Lorem Ipsum is simply dum my text of the</p></div>

<div class="abs web-panel"><div class="bar">Dashboard</div></div>
<div class="abs mobile-panel">
  <div class="mobile-drawer">
    <div class="user">Mara Lindqvist<br><span style="font-weight:400;font-size:4.8px">Volunteer</span></div>
    <ul><li>Dashboard</li><li class="sel">Notifications</li><li>Profile</li><li>Tasks</li><li>Incidents</li><li>Teams</li><li>Share</li><li>Logout</li></ul>
  </div>
</div>
<div class="badge-circle" style="left:374px;top:443px;width:40px;height:40px;background:var(--blue)">Web<br>Console</div>
<div class="badge-circle" style="left:432px;top:483px;width:40px;height:40px;background:var(--green)">Mobile<br>Application</div>

<div class="btn btn-blue" style="left:222px;top:595px;width:112px">WEB APPLICATION</div>
<div class="btn btn-green" style="left:339px;top:595px;width:113px">MOBILE APPLICATION</div>

<section class="abs respond"></section>
<h2 class="section-title respond-title">RESPONDING TO AN INCIDENT WITH</h2>

<div class="abs task-screen">
  <div class="bar">Manage Task</div>
  <div class="task-card">damage assessments<br>Damage Assessment<b>250 min</b><i>Jul 11, 2016 05:38 PM</i></div>
  <div class="task-card">task2<br>Debris Removal<b>45 min</b><i>Jul 11, 2016 06:37 PM</i></div>
  <div class="task-card">Supply Food<br>Supply Distribution<b>50 min</b><i>Jul 11, 2016 06:54 PM</i></div>
  <div class="fab">+</div>
</div>

<div class="feature left" style="left:110px;top:726px"><h3>Incident Management</h3><p>Lorem Ipsum is simply dummy text of the printing and typesetting industry.</p></div>
<div class="feature left" style="left:110px;top:826px"><h3>Team Management</h3><p>Lorem Ipsum is simply dummy text of the printing and typesetting industry.</p></div>
<div class="feature" style="left:442px;top:726px"><h3>Task Management</h3><p>Lorem Ipsum is simply dummy text of the printing and typesetting industry.</p></div>
<div class="feature" style="left:442px;top:826px"><h3>Communication Management</h3><p>Lorem Ipsum is simply dummy text of the printing and typesetting industry.</p></div>

<div class="icon-ring" style="left:241px;top:726px"></div>
<div class="icon-ring" style="left:241px;top:825px"></div>
<div class="icon-ring" style="left:408px;top:726px"></div>
<div class="icon-ring" style="left:408px;top:825px"></div>
<svg class="abs" style="left:0;top:720px" width="674" height="140" aria-hidden="true" fill="none" stroke="#fff" stroke-width="1.3">
  <rect x="248" y="13" width="10" height="10"/><path d="M250 18 l2 3 l5 -6"/>
  <circle cx="250" cy="117" r="2"/><circle cx="256" cy="117" r="2"/><path d="M246 124 q4 -5 8 0 M252 124 q4 -5 8 0"/>
  <path d="M414 23 l3 -6 l3 3 l3 -5 l3 8 z" fill="#fff"/>
  <path d="M414 121 a6 6 0 0 1 12 0 M414 121 v3 M426 121 v3"/>
</svg>

<section class="abs why">
  <h2 style="left:96px;top:17px">WHY ADOPT RV7</h2>
  <ul style="left:96px;top:44px;line-height:14.8px">
    <li>Easy system to register volunteers</li>
    <li>Accurate identification of number of CERT Volunteers available to help in an incident</li>
    <li>Efficient Communication mechanism to reach out to the volunteers via SMS</li>
    <li>Rich graphical visualization of Incidents &amp; Damages associated with the incidents</li>
  </ul>
  <div class="btn btn-green" style="left:97px;top:108px;width:62px;height:21px">LEARN MORE</div>

  <h2 style="left:354px;top:17px">REPORTS CONSOLE</h2>
  <ul style="left:354px;top:44px;width:220px;line-height:12.5px">
    <li>City Officials and Emergency Management Officials can get access to instant statistics on</li>
  </ul>
  <div class="arrow" style="top:73px">&#10140;&nbsp; Incident Management</div>
  <ul class="sub" style="left:366px;top:83px;font-size:5.2px;line-height:8.5px">
    <li>How many volunteers</li><li>Volunteer hours</li><li>Tasks involved</li><li>Supplies distributed</li><li>Teams involved</li>
  </ul>
  <div class="arrow" style="top:130px">&#10140;&nbsp; Volunteer Management</div>
  <div class="arrow" style="top:145px">&#10140;&nbsp; Damage Assessment</div>
  <div class="btn btn-green" style="left:358px;top:163px;width:61px;height:20px">LEARN MORE</div>
</section>
<div class="abs divider"></div>

<footer class="abs site-footer">
  <nav class="foot-nav"><span>Home</span><span>About Us</span><span>Resource management</span><span>Volunteer</span><span>Testimonials</span><span>Contact Us</span></nav>
  <div class="social" aria-label="Social links"><span></span><span></span><span></span><span></span><span></span><span class="hl"></span><span></span><span></span></div>
  <p class="copy">Copyright ©2016. www.rv7suite.example</p>
</footer>

</body>
</html>
```